Preisliste für Kosmetikinstitut
Zielgruppe
Ich benötige für mein Kosmetikinstitut eine Preisliste für die moderne Frau, aber auch Männer. Das Design sollte mein Logo enthalten. Farben des Designkonzepts einbauen.
A4 quer zum Falten, wie ein Heft, 1. Seite Preisliste mit logo, im Innenteil dann Anwendungen
Aufgabenstellung
Minimalistisch, ästhetisch, modern, edel
Kontaktdaten auf der Rückseite
LB Hautatelier
Lotte Brenner
Lindenhang 17
83671 Waakirchen
EMail: lotte@lb-hautatelier.de
Whatsapp: 0176 284 9017

```html
<!DOCTYPE html>
<html lang="de">
<head>
<meta charset="utf-8">
<title>Preisliste – Behandlungen</title>
<link href="https://fonts.googleapis.com/css2?family=Inter+Tight:wght@300;400&display=swap" rel="stylesheet">
<style>
  :root{
    --gold:#cbae68;
    --paper:#fbfaf2;
    --ink:#6b6d6c;
    --ink-soft:#767877;
    --canvas:#ffffff;
  }
  html,body{margin:0;padding:0;width:1200px;height:1200px;overflow:hidden;background:var(--canvas);}
  body{font-family:"Inter Tight",Helvetica,Arial,sans-serif;font-weight:300;color:var(--ink);}
  .spread{position:absolute;left:44px;top:199px;width:1792px;height:1267px;transform:scale(0.625);transform-origin:0 0;display:flex;}
  .page{position:relative;width:882px;height:1267px;background:var(--paper);}
  .spine{width:27px;height:1267px;background:var(--gold);}
  .page-title{position:absolute;top:64px;margin:0;font-weight:300;font-size:47px;letter-spacing:-1px;color:var(--gold);line-height:56px;}
  .page--left .page-title{left:69px;}
  .page--right .page-title{right:82px;}
  .treatment{position:absolute;left:141px;width:614px;}
  .page--right .treatment{left:143px;width:612px;}
  .treatment h3{margin:0;font-weight:300;font-size:23px;letter-spacing:-0.3px;color:var(--ink);line-height:26px;white-space:nowrap;}
  .treatment p{margin:0;font-size:14.5px;line-height:18px;letter-spacing:-0.2px;color:var(--ink-soft);}
  .treatment .gap{margin-top:10px;}
  .price{display:flex;justify-content:flex-end;gap:32px;font-size:18px;letter-spacing:-0.2px;margin-top:4px;padding-right:6px;}
  .steps{margin:18px 0 0;padding:0;list-style:none;font-size:14.5px;line-height:18px;letter-spacing:-0.2px;color:var(--ink-soft);}
  .steps li{padding-left:14px;text-indent:-14px;}
  .rows{margin-top:26px;font-size:18px;letter-spacing:-0.2px;}
  .rows div{display:flex;justify-content:space-between;line-height:22px;}
  .rows.spaced div{line-height:27px;}
  .dots{position:absolute;top:1196px;left:0;}
  .dot{position:absolute;width:32px;height:32px;border-radius:50%;background:var(--gold);}
</style>
</head>
<body>
<div class="spread">
  <section class="page page--left">
    <h2 class="page-title">Gesichtsbehandlungen</h2>

    <article class="treatment" style="top:164px">
      <h3>Express Facial Treatment</h3>
      <p>Für alle, die wenig Zeit haben und trotzdem ihre Haut auffrischen und revitalisieren wollen.</p>
      <p class="gap">Reinigung, Enzympeeling, Serum, Maske, Abschlusspflege</p>
      <div class="price"><span>35-45 Min.</span><span>€ 59,00</span></div>
    </article>

    <article class="treatment" style="top:283px">
      <h3>Classic Facial Treatment – Klassische Gesichtsbehandlung</h3>
      <p>Reinigung, Enzympeeling, Vapozon, Ausreinigung, Augenbrauenkorrektur, Ampulle, Maske, individuelle Abschlusspflege</p>
      <div class="price"><span>45-60 Min.</span><span>€ 89,00</span></div>
    </article>

    <article class="treatment" style="top:389px">
      <h3>Clear Skin Treatment</h3>
      <p>Die Haut wirkt ausgeglichener, Unreinheiten wird vorgebeugt, der Teint erhält Balance und kann sich beruhigen. Gleichzeitig wird die Haut durch die Hyaluronsäure vitalisiert und Falten und Fältchen kann entgegengewirkt werden.</p>
      <div class="price"><span>50-60 Min.</span><span>€ 89,00</span></div>
    </article>

    <article class="treatment" style="top:514px">
      <h3>Vasculine Treatment</h3>
      <p>Hautrötungen und Couperose Erscheinungen werden gelindert, die Gefäßwände werden gestärkt und das Hautbild wirkt ausgeglichener, mögliche Irritationen gehen zurück. Gleichzeitig sorgt die hochkonzentrierte Hyaluronsäure für Frische, Vitalität und Glätte.</p>
      <div class="price"><span>50-60 Min.</span><span>€ 89,00</span></div>
    </article>

    <article class="treatment" style="top:659px">
      <h3>Tendrelle Soft Treatment (für die empfindliche, gereizte Haut)</h3>
      <p>Entzündliche Prozesse können gemildert werden, gereizte Haut oder solche, die wenig verträgt, wird beruhigt. Irritationen können zurückgehen, die Haut erhält Balance.</p>
      <div class="price"><span>ca. 50 Min.</span><span>€ 79,00</span></div>
    </article>

    <article class="treatment" style="top:787px">
      <h3>Vitamin Soft Boost</h3>
      <p>Vitamine sorgen für Power und Frische in und auf der Haut, die Widerstandskraft der Haut wird gestärkt. Die Faltentiefe kann gemildert werden.</p>
      <div class="price"><span>ca. 50 Min.</span><span>€ 79,00</span></div>
    </article>

    <article class="treatment" style="top:915px">
      <h3>Anti-Age Advanced</h3>
      <p>Die Haut wirkt insgesamt erfrischt, vitalisiert und gestrafft. Feine Linien und Fältchen werden reduziert.</p>
      <div class="price" style="gap:50px"><span>50-70 Min.&nbsp; (je nach Peeling)</span><span>€ 99,00</span></div>
    </article>

    <article class="treatment" style="top:1044px">
      <h3>Chemisches Peeling (Oktober – April)</h3>
      <p>Professionelle Peelings können viele Problemstellungen lindern, verbessern oder gar beheben. Dazu gehören die Zellerneuerung, Glättung der Hauttextur, Reduzierung von Pigmentflecken, Verbesserung von Akne</p>
    </article>

    <div class="dots">
      <span class="dot" style="left:383px"></span>
      <span class="dot" style="left:452px"></span>
    </div>
  </section>

  <div class="spine"></div>

  <section class="page page--right">
    <h2 class="page-title">Apparative Behandlungen</h2>

    <article class="treatment" style="top:164px">
      <h3>AQUAlumen – „Glowing Skin“ Treatment</h3>
      <p>In 6 Schritten zu einer Haut mit einmaligem Glow- Effekt</p>
      <ol class="steps">
        <li>1. Behandlungsschritt: die Haut wird tiefengereinigt</li>
        <li>2. Behandlungsschritt: die obersten Verhornungen und Schuppen werden sanft mit einem Peeling gelöst</li>
        <li>3. Behandlungsschritt: die Haut wird in der Tiefe gereinigt und entschlackt</li>
        <li>4. Behandlungsschritt: niedermolekulare Wirkstoffe werden aufgebracht, um die Haut zu erfrischen und den entsprechenden Glow zu geben</li>
        <li>5. Ausgewählte und hochdosierte Wirkstoffessenzen werden auf die Haut gesprüht und durch die niedrige Molekularstruktur können diese tiefer in der Haut wirken</li>
        <li>6. Zum Schluss werden die Essenzen durch eine Impulsgebende Druckluftmassage noch tiefer in die Haut gebracht</li>
      </ol>
      <div class="price"><span>60 Min.</span><span>€ 140,00</span></div>
    </article>

    <article class="treatment" style="top:454px">
      <h3>Mikrodermabrasion</h3>
      <p>Bei der Mikrodermabrasion handelt es sich um ein mechanisches Hautpeeling, dabei werden mittels feinster Kristalle die Hornzellen der obersten Hautschicht schonend abgetragen und dann mit Hilfe eines Unterdrucks behutsam abgesaugt. Der revitalisierende Prozess erhöht die Durchblutung, fördert die Zellerneuerung und verleiht ihrer Haut ein zartes frisches Gefühl. Die Haut gewinnt an Spannkraft, feine Fältchen werden gemildert und Poren sichtbar verkleinert. Außerdem hilft es bei oberflächlichen Akne Narben, Pigmentstörungen und Dehnungsstreifen. Wirkstoffe können nun wieder besser von der Haut aufgenommen werden.</p>
      <div class="rows spaced">
        <div><span>Gesicht</span><span>€ &nbsp;89,00</span></div>
        <div><span>Gesicht, Hals, Dekolleté</span><span>€ 110,00</span></div>
      </div>
    </article>

    <article class="treatment" style="top:708px">
      <h3>Microneedling</h3>
      <p>Die Behandlung eignet sich besonders für Menschen, die ihre Hautqualität verbessern und Falten, (Akne)Narben, Pigmentverschiebungen, große Poren und sogar Haarausfall behandeln wollen. Mit Hilfe feinster Nadeln werden der Haut kontrolliert Mikroverletzungen zugeführt, dies regt die natürliche Wundheilung, sowie Kollagen- und Elastin Bildung an. Microneedling ist also eine natürliche Beauty-Behandlung, die körpereigene Reparaturmechanismen nutzt, um ein strafferes Hautbild zu erhalten. Bereits nach der ersten Behandlung sieht die Haut aufgepolstert, frisch und rosig aus. Kleine Linien und Fältchen werden tiefenbehandelt. Die Haut wirkt straffer und jugendlicher. Ein weiterer Vorteil, durch die Stichkanäle können Wirkstoffe besser von der Haut aufgenommen werden.</p>
      <div class="rows">
        <div><span>Gesicht</span><span>€ 110,00</span></div>
        <div><span>Gesicht, Hals</span><span>€ 130,00</span></div>
        <div><span>Gesicht, Hals, Dekolleté</span><span>€ 150,00</span></div>
      </div>
    </article>

    <article class="treatment" style="top:1034px">
      <h3>Zusatzleistungen</h3>
      <div class="rows">
        <div><span>Augenbrauen zupfen</span><span>€ 8</span></div>
        <div><span>Augenbrauen färben</span><span>€ 12</span></div>
        <div><span>Wimpern färben</span><span>€ 15</span></div>
        <div><span>Enthaarung störender Gesichtsbehaarung mittels Wax</span><span>€ 10-30</span></div>
      </div>
    </article>

    <div class="dots">
      <span class="dot" style="left:366px"></span>
      <span class="dot" style="left:444px"></span>
      <span class="dot" style="left:513px"></span>
    </div>
  </section>
</div>
</body>
</html>
```